Software Product Flyer Design

A established czech software company needs a marketing flyer to promote their software product and its modules.
The overall feel of the flyer must to be serious, but also eye-catching, enticing, clever and bold to attract customers.
Unifying graphic element is the new product logo.
The flyer would be A4, colour both sides and folded once (to give 4 pages of A5).
Title page - product logo with module name and module icon, short presentation of the product and list of its key features.
Inside pages - detailed informations with screenshots or graphical schemas.
Back side - informations about technical requirements and user support, contacts (address, phone, fax, e-mail, web pages - no social networks).
Product logo, module icon and some images attached.
Updates
Hello,
Reason: For organizational reasons we extending the deadline by 10 days.
FYI: We have uploaded the new ZIP file with previous version of our flyer.
Attached PDF file with text for inner pages.
Target Market(s)
Existing or new customers like municipalities, public authorities and nonprofit organizations.
Industry/Entity Type
Marketing
Requirements
Must have
- Winning designer must provide a template for Adobe InDesign based on his graphic design.
Avoid to using exotic fonts - in Czech we use Latin Extended characters (like áéěíýůčřžšťďň).
Nice to have
- Using graphic motif from product logo like as attached splash screen.

```html
<!DOCTYPE html>
<html lang="en">
<head>
<meta charset="utf-8">
<title>Verano – Software Product Flyer</title>
<link rel="stylesheet" href="https://fonts.googleapis.com/css2?family=Arimo:wght@400;700&display=swap">
<style>
  :root {
    --orange: #f15a22;
    --black: #0b0b0b;
    --paper: #efefef;
    --heading-grey: #6d6e71;
    --text: #231f20;
    --white: #ffffff;
  }
  * { box-sizing: border-box; margin: 0; padding: 0; }
  html, body { width: 1200px; height: 848px; overflow: hidden; background: var(--paper); }
  body { font-family: "Arimo", Arial, sans-serif; color: var(--text); }

  .flyer { position: relative; width: 1200px; height: 848px; overflow: hidden; background: var(--paper); }
  .flyer__shapes { position: absolute; inset: 0; width: 1200px; height: 848px; display: block; }

  .brand { position: absolute; left: 48px; top: 44px; display: flex; align-items: center; gap: 16px; }
  .brand__square { width: 52px; height: 52px; background: var(--orange); border-radius: 6px; }
  .brand__name { font-weight: 700; font-size: 92px; line-height: 1; color: var(--white); letter-spacing: -2px; }

  .section-title { position: absolute; display: flex; align-items: flex-end; gap: 6px; }
  .section-title__mark { width: 10px; height: 10px; background: var(--orange); margin-bottom: 6px; }
  .section-title__text {
    font-weight: 700; font-size: 24px; line-height: 1; color: var(--heading-grey);
    padding-bottom: 3px; border-bottom: 2px solid var(--orange); padding-right: 36px;
  }
  .section-title--right { left: 732px; top: 108px; }
  .section-title--left { left: 6px; top: 534px; }

  .copy { position: absolute; font-size: 9.6px; line-height: 13px; }
  .copy p { margin: 0; }
  .copy strong { display: block; font-weight: 700; }
  .copy--intro-right { left: 750px; top: 152px; width: 432px; text-align: center; }
  .copy--detail-right { left: 862px; top: 264px; width: 318px; text-align: center; }
  .copy--intro-left { left: 29px; top: 582px; width: 322px; text-align: justify; }
  .copy--detail-left { left: 29px; top: 704px; width: 428px; text-align: justify; }
  .copy--band { color: var(--white); top: 696px; }
  .copy--band-first { left: 636px; width: 214px; text-align: justify; }
  .copy--band-second { left: 869px; width: 218px; }

  .tile-label {
    position: absolute; width: 180px; text-align: center; color: var(--white);
    font-weight: 700; font-size: 13px; line-height: 16px; text-transform: uppercase;
  }
  .tile-label--features { left: 600px; top: 310px; }
  .tile-label--savings { left: 468px; top: 436px; }
  .tile-label--speed { left: 338px; top: 566px; }
</style>
</head>
<body>
<main class="flyer">
  <svg class="flyer__shapes" viewBox="0 0 1000 707" preserveAspectRatio="none">
    <defs>
      <linearGradient id="office-tones" x1="0" y1="0" x2="1" y2="1">
        <stop offset="0" stop-color="#c9d3dc"/>
        <stop offset="0.5" stop-color="#7d8793"/>
        <stop offset="1" stop-color="#3a3f48"/>
      </linearGradient>
      <linearGradient id="couple-tones" x1="0" y1="0" x2="1" y2="1">
        <stop offset="0" stop-color="#b7bcc4"/>
        <stop offset="0.45" stop-color="#c9a487"/>
        <stop offset="1" stop-color="#2e3444"/>
      </linearGradient>
    </defs>

    <polygon class="photo photo--team" role="img" aria-label="Photo: business team in a bright office, smiling woman in front"
      points="0,145 590,145 465,240 250,455 0,205" fill="url(#office-tones)"/>
    <polygon class="photo photo--users" role="img" aria-label="Photo: couple working together on a laptop"
      points="680,238 1000,558 1000,562 360,562 575,345" fill="url(#couple-tones)"/>

    <polygon class="band band--top" points="0,0 445,0 590,145 0,145" fill="var(--black)"/>
    <polygon class="band band--bottom" points="360,560 1000,560 1000,707 507,707" fill="var(--black)"/>

    <polygon class="tile tile--features" points="575,130 680,238 575,345 467,240" fill="var(--orange)"/>
    <polygon class="tile tile--savings" points="465,240 572,348 465,455 358,348" fill="var(--black)"/>
    <polygon class="tile tile--speed" points="357,348 463,455 357,560 250,455" fill="var(--orange)"/>

    <polyline class="icon icon--tick" points="542,202 563,223 606,180" fill="none" stroke="var(--white)" stroke-width="12" stroke-linecap="square"/>

    <g class="icon icon--savings" fill="var(--white)">
      <ellipse cx="463" cy="318" rx="28" ry="18"/>
      <rect x="444" y="328" width="8" height="15" rx="2"/>
      <rect x="470" y="328" width="8" height="15" rx="2"/>
      <rect x="487" y="311" width="9" height="9" rx="2"/>
      <polygon points="446,303 453,292 457,305"/>
      <circle cx="472" cy="290" r="8" fill="var(--orange)"/>
    </g>

    <g class="icon icon--speed">
      <circle cx="357" cy="420" r="20" fill="none" stroke="var(--white)" stroke-width="5"/>
      <line x1="357" y1="422" x2="368" y2="411" stroke="var(--white)" stroke-width="4" stroke-linecap="round"/>
      <circle cx="357" cy="422" r="4" fill="var(--white)"/>
    </g>
  </svg>

  <div class="brand">
    <span class="brand__square"></span>
    <span class="brand__name">Verano</span>
  </div>

  <h2 class="section-title section-title--right"><span class="section-title__mark"></span><span class="section-title__text">INFOMATION</span></h2>
  <div class="copy copy--intro-right">
    <p>Lorem ipsum dolor sit amet, consectetur adipiscing elit. Nam eu urna eget massa tristique placerat. Nulla vestibulum feugiat vestibulum. Suspendisse potenti. Nam vel tortor mi. Duis sed felis id quam tristique porta et ac nulla. Sed convallis volutpat viverra. Fusce mattis lacus posuere sapien suscipit nec congue risus sagittis. Nam ut sem eget eros lobortis ornare eu id felis. Etiam enim nisl, tincidunt vitae mattis non, mollis sed neque.</p>
  </div>
  <div class="copy copy--detail-right">
    <strong>Lorem ipsum dolor sit amet</strong>
    <p>consectetur adipiscing elit. Nam eu urna eget massa tristique placerat. Nulla vestibulum feugiat vestibulum. Suspendisse potenti. Nam vel tortor mi. Duis sed felis id quam tristique porta et ac nulla. Sed convallis volutpat viverra. Fusce mattis lacus posuere sapien suscipit nec congue risus sagittis. Nam ut sem eget eros lobortis ornare eu id felis. Etiam enim nisl, tincidunt vitae mattis non, mollis sed neque. v</p>
  </div>

  <div class="tile-label tile-label--features">Lorem ipsum<br>dolor sit amet</div>
  <div class="tile-label tile-label--savings">Lorem ipsum<br>dolor sit amet</div>
  <div class="tile-label tile-label--speed">Lorem ipsum<br>dolor sit amet</div>

  <h2 class="section-title section-title--left"><span class="section-title__mark"></span><span class="section-title__text">INFOMATION</span></h2>
  <div class="copy copy--intro-left">
    <p>Lorem ipsum dolor sit amet, consectetur adipiscing elit. Nam eu urna eget massa tristique placerat. Nulla vestibulum feugiat vestibulum. Suspendisse potenti. Nam vel tortor mi. Duis sed felis id quam tristique porta et ac nulla. Sed convallis volutpat viverra. Fusce mattis lacus posuere sapien suscipit nec congue risus sagittis. Nam ut sem eget eros lobortis ornare eu id felis. Etiam enim nisl, tincidunt vitae mattis non, mollis sed neque.</p>
  </div>
  <div class="copy copy--detail-left">
    <strong>Lorem ipsum dolor sit amet</strong>
    <p>consectetur adipiscing elit. Nam eu urna eget massa tristique placerat. Nulla vestibulum feugiat vestibulum. Suspendisse potenti. Nam vel tortor mi. Duis sed felis id quam tristique porta et ac nulla. Sed convallis volutpat viverra. Fusce mattis lacus posuere sapien suscipit nec congue risus sagittis. Nam ut sem eget eros lobortis ornare eu id felis. Etiam enim nisl, tincidunt vitae mattis non, mollis sed neque.</p>
  </div>

  <div class="copy copy--band copy--band-first">
    <p>Lorem ipsum dolor sit amet, consectetur adipiscing elit. Nam eu urna eget massa tristique placerat. Nulla vestibulum feugiat vestibulum. Suspendisse potenti. Nam vel tortor mi. Duis sed felis id quam tristique porta et ac nulla. Sed convallis volutpat viverra. Fusce mattis lacus posuere sapien suscipit nec congue risus sagittis.</p>
  </div>
  <div class="copy copy--band copy--band-second">
    <p>Nam ut sem eget eros lobortis ornare eu id felis. Etiam enim nisl, tincidunt vitae mattis non, mollis sed neque.</p>
  </div>
</main>
</body>
</html>
```